Business Card Design - Amberfield Court

We are looking at a new design for our business cards that has a modern and professional look. We run a residential aged care facility focussing on the care of residents. The cards will be used for potential clients, consultants and business opportunities in this sector. Blue and white is our main colours and would to see these colours incorporated in the design.
Industry/Entity Type
Business
Contact Information for Business Card
Amberfield Court, Darren Walsh, dwalsh@amberfieldcourt.com.au, Finance Manager, 0472 639 208, BCom, 37 Marrabel Crescent, Brindle Vale, Qld 4093.
Look and feel
Each slider illustrates characteristics of the customer's brand and the style your logo design should communicate.

```html
<!DOCTYPE html>
<html lang="en">
<head>
<meta charset="utf-8">
<title>Amberfield Court – Business Card</title>
<link rel="stylesheet" href="https://fonts.googleapis.com/css2?family=Open+Sans:wght@400;700&display=swap">
<style>
  :root {
    --navy: #1d3a4a;
    --navy-soft: #2c5266;
    --accent: #5e8fb0;
    --white: #ffffff;
    --backdrop: #e9edf0;
  }
  * { margin: 0; padding: 0; box-sizing: border-box; }
  html, body { width: 1200px; height: 900px; overflow: hidden; background: var(--backdrop); }
  body { position: relative; font-family: "Open Sans", sans-serif; }

  .card {
    position: absolute;
    width: 600px;
    height: 343px;
    border-radius: 22px;
    overflow: hidden;
    box-shadow: 0 10px 28px rgba(0,0,0,0.18);
  }
  .card--front { left: 110px; top: 80px; background: var(--navy); }
  .card--back  { left: 490px; top: 477px; background: var(--white); }

  .front-emblem {
    position: absolute;
    left: 150px;
    top: 115px;
    width: 330px;
    height: 330px;
    border-radius: 50%;
    background: linear-gradient(160deg, var(--white) 0%, #dfe7ec 55%, #c9d6de 100%);
  }

  .back-wave { position: absolute; inset: 0; width: 100%; height: 100%; }

  .brand {
    position: absolute;
    left: 30px;
    top: 140px;
    width: 250px;
    display: flex;
    flex-direction: column;
    align-items: center;
    gap: 10px;
  }
  .brand__row { display: flex; align-items: center; gap: 8px; white-space: nowrap; }
  .brand__dot { flex: none; width: 14px; height: 14px; border-radius: 50%; background: var(--navy); }
  .brand__name {
    color: var(--navy);
    font-weight: 700;
    font-size: 19px;
    letter-spacing: 0.8px;
    text-transform: uppercase;
  }
  .brand__tagline {
    background: var(--navy);
    color: var(--white);
    font-size: 12.5px;
    padding: 3px 12px;
    letter-spacing: 0.3px;
    white-space: nowrap;
  }

  .contact {
    position: absolute;
    left: 368px;
    top: 112px;
    color: var(--white);
    font-size: 12.5px;
    line-height: 1.45;
    white-space: nowrap;
  }
  .contact__name { font-weight: 700; font-size: 21px; line-height: 1.1; letter-spacing: 0.5px; }
  .contact__role { font-size: 11px; text-transform: uppercase; margin-bottom: 10px; }
  .contact__line { display: flex; align-items: center; gap: 7px; }
  .contact__line svg { width: 11px; height: 11px; flex: none; }
  .contact__gap { height: 4px; }
</style>
</head>
<body>

<section class="card card--front" aria-label="Card front">
  <div class="front-emblem" role="img" aria-label="Large emblem area: carer and resident figures inside a white circle"></div>
</section>

<section class="card card--back" aria-label="Card back">
  <svg class="back-wave" viewBox="0 0 600 343" preserveAspectRatio="none" aria-hidden="true">
    <path d="M252 0 C 330 40, 320 140, 345 220 C 365 285, 400 330, 470 343 L 600 343 L 600 0 Z" fill="var(--navy)"/>
    <path d="M236 0 C 318 36, 306 140, 330 222 C 350 290, 390 330, 458 343" fill="none" stroke="var(--accent)" stroke-width="7"/>
  </svg>

  <div class="brand">
    <div class="brand__row">
      <span class="brand__dot"></span>
      <span class="brand__name">Amberfield Court</span>
    </div>
    <span class="brand__tagline">Care, Comfort, Companionship</span>
  </div>

  <div class="contact">
    <div class="contact__name">DARREN WALSH</div>
    <div class="contact__role">Finance Manager (BCom)</div>
    <div>37 Marrabel Crescent</div>
    <div>Brindle Vale, Qld 4093</div>
    <div class="contact__gap"></div>
    <div class="contact__line">
      <svg viewBox="0 0 24 24"><path fill="#fff" d="M6.6 10.8a15.1 15.1 0 0 0 6.6 6.6l2.2-2.2a1 1 0 0 1 1-.25 11.4 11.4 0 0 0 3.6.57 1 1 0 0 1 1 1V20a1 1 0 0 1-1 1A17 17 0 0 1 3 4a1 1 0 0 1 1-1h3.5a1 1 0 0 1 1 1c0 1.25.2 2.450.57 3.57a1 1 0 0 1-.25 1z"/></svg>
      <span>0472 639 208</span>
    </div>
    <div class="contact__line">
      <svg viewBox="0 0 24 24"><rect x="2" y="5" width="20" height="14" rx="1.5" fill="none" stroke="#fff" stroke-width="2"/><path d="M3 6l9 7 9-7" fill="none" stroke="#fff" stroke-width="2"/></svg>
      <span>dwalsh@amberfieldcourt.com.au</span>
    </div>
  </div>
</section>

</body>
</html>
```